The most modern business card ever !!!

Our company call “Vendalo”. Vendalo is a technology company specialized in cruises solutions. Out main product is a platform to reserve cruises. This is a revolutionary platform that make easier to travel agencies and final users to reserve cruises across dozen companies like tibba, wernu, hpv, dgb, etc..We are a “start up”, with a young team of developers and we want to transmit it.. For it, we want something different, a modern business card that represent cruises and technology.. When someone receive this card, this person should say: wowww this is different… this is modern… this is a cruise related company..
- diferent, modern
- traditions business card

```html
<!DOCTYPE html>
<html lang="en">
<head>
<meta charset="utf-8">
<title>Vendalo – Business Card</title>
<link rel="stylesheet" href="https://fonts.googleapis.com/css2?family=Lato:wght@400;700&family=Crimson+Text&display=swap">
<style>
  :root {
    --page-bg: #d6d9dc;
    --card-top: #f1f3f4;
    --card-bottom: #e2e5e7;
    --card-edge: rgba(255, 255, 255, 0.9);
    --ink: #141414;
    --deco-blue: #1d72ad;
    --deco-soft: rgba(29, 114, 173, 0.10);
    --accent-blue: #2a86d1;
    --row-bg: rgba(40, 50, 60, 0.09);
    --icon-line: #ffffff;
  }
  * { margin: 0; padding: 0; box-sizing: border-box; }
  html, body {
    width: 967px;
    height: 1200px;
    overflow: hidden;
    background: var(--page-bg);
  }
  .canvas {
    position: relative;
    width: 967px;
    height: 1200px;
  }
  .card {
    position: absolute;
    left: 204px;
    top: 100px;
    width: 559px;
    height: 1000px;
    border-radius: 30px;
    overflow: hidden;
    background: linear-gradient(180deg, var(--card-top), var(--card-bottom));
    border: 2px solid var(--card-edge);
    box-shadow: 0 10px 40px rgba(0, 0, 0, 0.18);
    font-family: "Lato", Arial, sans-serif;
    color: var(--ink);
  }
  .card__decoration {
    position: absolute;
    left: 0;
    top: 180px;
    width: 100%;
    height: 310px;
    background: linear-gradient(180deg, var(--deco-soft) 0%, rgba(29, 114, 173, 0.55) 55%, var(--deco-soft) 100%);
  }
  .brand-name {
    position: absolute;
    top: 82px;
    left: 0;
    width: 100%;
    text-align: center;
    font-size: 68px;
    font-weight: 700;
    letter-spacing: 1px;
    line-height: 1;
    color: var(--ink);
  }
  .person-name {
    position: absolute;
    top: 521px;
    left: 0;
    width: 100%;
    text-align: center;
    font-size: 34px;
    font-weight: 400;
    line-height: 1;
  }
  .job-title {
    position: absolute;
    top: 570px;
    left: 0;
    width: 100%;
    text-align: center;
    font-family: "Crimson Text", Georgia, serif;
    font-size: 23px;
    color: var(--accent-blue);
    line-height: 1;
  }
  .title-rule {
    position: absolute;
    top: 619px;
    left: 239px;
    width: 81px;
    height: 4px;
    background: var(--accent-blue);
  }
  .contact-list {
    position: absolute;
    left: 36px;
    top: 690px;
    width: 491px;
    list-style: none;
  }
  .contact-row {
    display: flex;
    align-items: center;
    height: 78px;
    margin-bottom: 16px;
    background: var(--row-bg);
  }
  .contact-row__icon {
    width: 83px;
    height: 78px;
    background: var(--accent-blue);
    display: flex;
    align-items: center;
    justify-content: center;
    flex-shrink: 0;
  }
  .contact-row__icon svg { width: 42px; height: 42px; }
  .contact-row__text {
    flex: 1;
    text-align: right;
    padding-right: 10px;
    font-size: 24px;
    color: var(--ink);
  }
</style>
</head>
<body>
<main class="canvas">
  <article class="card">
    <div class="card__decoration" role="img" aria-label="Decorative blue band across the middle of the card"></div>

    <h1 class="brand-name">Vendalo</h1>

    <h2 class="person-name">YOUR NAME</h2>
    <p class="job-title">Job title</p>
    <div class="title-rule"></div>

    <ul class="contact-list">
      <li class="contact-row">
        <span class="contact-row__icon">
          <svg viewBox="0 0 42 42" fill="none" stroke="var(--icon-line)" stroke-width="1.6">
            <circle cx="21" cy="21" r="19"/>
            <path d="M15 12c1.5-1 3-.5 3.5 1l1 3c.3 1-.3 1.7-1.2 2.2 1 2.3 2.6 4 4.6 5 .6-.9 1.3-1.5 2.3-1.2l3 1c1.5.5 2 2 1 3.5-1 1.5-3 2.2-5 1.4C17.5 26 14 22 13.2 17c-.4-2 .3-4 1.8-5z" fill="var(--icon-line)" stroke="none"/>
          </svg>
        </span>
        <span class="contact-row__text">000 000 0000</span>
      </li>
      <li class="contact-row">
        <span class="contact-row__icon">
          <svg viewBox="0 0 42 42" fill="none" stroke="var(--icon-line)" stroke-width="1.6">
            <circle cx="21" cy="21" r="19"/>
            <rect x="12" y="15" width="18" height="12" fill="var(--icon-line)" stroke="none"/>
            <path d="M12 15l9 7 9-7" stroke="var(--accent-blue)" stroke-width="1.4"/>
          </svg>
        </span>
        <span class="contact-row__text">youremail@xyz.com</span>
      </li>
      <li class="contact-row">
        <span class="contact-row__icon">
          <svg viewBox="0 0 42 42" fill="none" stroke="var(--icon-line)" stroke-width="1.4">
            <circle cx="21" cy="21" r="19"/>
            <circle cx="21" cy="21" r="9"/>
            <ellipse cx="21" cy="21" rx="4" ry="9"/>
            <path d="M12 21h18M13.5 16.5h15M13.5 25.5h15"/>
          </svg>
        </span>
        <span class="contact-row__text">www.yourwebsite.com</span>
      </li>
    </ul>
  </article>
</main>
</body>
</html>
```